Client Meeting and installation Email Follow up

I would like a follow-up email template created.
Currently, we do a lot of new construction builds and meet with clients about 6-3 months before they take possession of their new house. I want a follow-up email template to be sent after the homeowner takes possession of their house that enquires if the clients are happy about their new lighting, the service they received, and their customer service representative with Brightwell Lamps and Breezes. I have attached a few files of what our current marketing looks like.
Target Market(s)
Home Owners We have already met with
Industry/Entity Type
Residential lighting
Font styles to use
Other font styles liked:
- Alta Light, Playfair Display, Montserrat
Colors
Designer to choose colors to be used in the design.
Look and feel
Each slider illustrates characteristics of the customer's brand and the style your logo design should communicate.

```html
<!DOCTYPE html>
<html lang="en">
<head>
<meta charset="utf-8">
<title>Brightwell Lamps and Breezes – Follow Up</title>
<link rel="stylesheet" href="https://fonts.googleapis.com/css2?family=Alegreya+Sans+SC:wght@500;700;800&family=Lato:wght@400&display=swap">
<style>
  :root {
    --tan: #d7b9a3;
    --mocha: #a58a7a;
    --mocha-dark: #9a7c6a;
    --ink: #111111;
    --heading-accent: #9b7b68;
    --body-text: #4a4a4a;
    --white: #ffffff;
    --hero-warm-1: #6a4a34;
    --hero-warm-2: #d9b894;
    --kitchen-1: #b8b2aa;
    --kitchen-2: #e9e6e1;
  }
  * { margin: 0; padding: 0; box-sizing: border-box; }
  html, body { width: 1200px; height: 3196px; overflow: hidden; background: var(--white); }
  .email { position: relative; width: 1200px; height: 3196px; background: var(--white); }
  .top-rule { position: absolute; left: 0; top: 0; width: 1200px; height: 11px; background: var(--tan); }

  .brand-name {
    position: absolute; left: 220px; top: 81px; width: 760px; height: 222px;
    display: flex; align-items: center; justify-content: center;
    font-family: "Alegreya Sans SC", sans-serif; font-weight: 800;
    font-size: 68px; line-height: 1.05; text-align: center; color: var(--ink);
  }

  .headline {
    position: absolute; left: 0; top: 370px; width: 1200px; text-align: center;
    font-family: "Alegreya Sans SC", sans-serif; font-weight: 800;
    font-size: 64px; line-height: 78px; color: var(--ink);
  }
  .headline .accent { display: block; color: var(--heading-accent); }

  .photo { position: absolute; }
  .hero-photo {
    left: 0; top: 568px; width: 1200px; height: 768px;
    background: radial-gradient(ellipse at 55% 30%, #f3dcc0 0%, var(--hero-warm-2) 40%, var(--hero-warm-1) 100%);
  }
  .kitchen-photo {
    left: 136px; top: 2198px; width: 1064px; height: 514px;
    background: linear-gradient(180deg, #d9d3cc 0%, var(--kitchen-2) 45%, var(--kitchen-1) 100%);
  }

  .block { position: absolute; }
  .bar-tall { left: 913px; top: 1255px; width: 89px; height: 365px; background: var(--tan); }
  .bar-short { left: 757px; top: 2090px; width: 77px; height: 108px; background: var(--tan); }
  .bar-mid { left: 877px; top: 1921px; width: 65px; height: 277px; background: var(--mocha-dark); }
  .kitchen-base { left: 73px; top: 2653px; width: 429px; height: 95px; background: var(--mocha); }

  .feedback-panel {
    position: absolute; left: 102px; top: 1110px; width: 576px; height: 970px;
    background: var(--mocha); color: var(--white); padding: 52px 50px 0 58px;
  }
  .feedback-panel h2 {
    font-family: "Alegreya Sans SC", sans-serif; font-weight: 800;
    font-size: 46px; line-height: 60px; letter-spacing: 1px; margin-bottom: 28px;
  }
  .topics { list-style: none; }
  .topic { position: relative; padding-left: 34px; margin-bottom: 30px; }
  .topic::before {
    content: ""; position: absolute; left: 0; top: 14px;
    width: 13px; height: 13px; border-radius: 50%; background: var(--white);
  }
  .topic h3 {
    font-family: "Alegreya Sans SC", sans-serif; font-weight: 500;
    font-size: 27px; line-height: 39px; margin-bottom: 12px;
  }
  .topic p { font-family: "Lato", sans-serif; font-size: 21.5px; line-height: 31.5px; }

  .intro {
    position: absolute; left: 76px; top: 2807px; width: 1000px;
    font-family: "Lato", sans-serif; font-size: 28px; line-height: 43.5px; color: var(--body-text);
  }

  .social { position: absolute; left: 77px; top: 3077px; display: flex; gap: 18px; }
  .social-link { width: 48px; height: 48px; border-radius: 5px; display: block; }
  .social-link.one { background: var(--mocha-dark); }
  .social-link.two { background: var(--tan); }
  .social-link.three { background: var(--mocha); }
  .social-link.four { background: var(--heading-accent); }
  .social-link.five { background: var(--mocha-dark); }
</style>
</head>
<body>
<main class="email">
  <div class="top-rule"></div>

  <div class="brand-name">Brightwell Lamps and Breezes</div>

  <h1 class="headline">We Hope You’re Loving Your <span class="accent">New Lighting!</span></h1>

  <div class="photo hero-photo" role="img" aria-label="Warmly lit bedroom with a brass chandelier above an upholstered headboard"></div>

  <div class="block bar-tall"></div>

  <section class="feedback-panel">
    <h2>Here are a few things we’d appreciate your feedback on:</h2>
    <ul class="topics">
      <li class="topic">
        <h3>Your Satisfaction with the Lighting:</h3>
        <p>Are you pleased with how the lighting enhances your new home? Are there any adjustments or additional features you would like to discuss?</p>
      </li>
      <li class="topic">
        <h3>The Installation Process:</h3>
        <p>Did our team meet your expectations during the installation? Was the process smooth and professional?</p>
      </li>
      <li class="topic">
        <h3>Customer Service Experience:</h3>
        <p>How did you find working with your Brightwell Lamps and Breezes representative? Were they helpful and responsive to your needs?</p>
      </li>
    </ul>
  </section>

  <div class="block bar-mid"></div>
  <div class="block bar-short"></div>

  <div class="photo kitchen-photo" role="img" aria-label="Kitchen with three concrete dome pendant lights over a white subway tile wall"></div>
  <div class="block kitchen-base"></div>

  <p class="intro">Congratulations on the recent move into your new home! We hope you’re settling in well and enjoying your new space. At Brightwell Lamps and Breezes, we’re dedicated to ensuring that every detail of your lighting installation meets your expectations. We’d love to hear about your experience with our services and the installation process.</p>

  <nav class="social" aria-label="Social media">
    <a class="social-link one" href="#" aria-label="Social profile 1"></a>
    <a class="social-link two" href="#" aria-label="Social profile 2"></a>
    <a class="social-link three" href="#" aria-label="Social profile 3"></a>
    <a class="social-link four" href="#" aria-label="Social profile 4"></a>
    <a class="social-link five" href="#" aria-label="Social profile 5"></a>
  </nav>
</main>
</body>
</html>
```